Business Card Design for Property Development Company Director

I am looking for a professional and unforgettable business card design for our Director of our Property Development Company.
Please see attached .pptx file to find out what information to include. You don't have to follow the exact format shown in the file - I am interested to see your creative flair using the information provided.

```html
<!DOCTYPE html>
<html lang="en">
<head>
<meta charset="utf-8">
<title>Halvern Property Group – Business Card</title>
<link href="https://fonts.googleapis.com/css2?family=Lato:wght@400;700&display=swap" rel="stylesheet">
<style>
  :root {
    --brand-blue: #1459a8;
    --text-grey: #5b5b5b;
    --card-white: #ffffff;
    --page-bg: #ecebe8;
    --line-blue: #1a5fb0;
  }
  * { margin: 0; padding: 0; box-sizing: border-box; }
  html, body {
    width: 1200px; height: 848px; overflow: hidden;
    background: var(--page-bg);
    font-family: "Lato", sans-serif;
  }
  .canvas { position: relative; width: 1200px; height: 848px; }
  .card {
    position: absolute;
    box-shadow: 0 6px 18px rgba(0,0,0,0.18);
  }
  .card-front {
    left: 251px; top: 28px; width: 672px; height: 380px;
    background: var(--card-white);
  }
  .card-back {
    left: 249px; top: 442px; width: 677px; height: 374px;
    background: var(--brand-blue);
    color: #fff;
  }
  .brand {
    display: flex; align-items: center; gap: 12px;
    font-weight: 700; letter-spacing: 0.5px;
  }
  .brand-mark { display: block; }
  .card-front .brand {
    position: absolute; left: 39px; top: 54px;
    color: var(--brand-blue); font-size: 27px;
  }
  .card-front .brand-mark { width: 42px; height: 42px; background: var(--brand-blue); }
  .contact-block {
    position: absolute; left: 338px; top: 159px;
    border-left: 2px solid var(--line-blue);
    padding-left: 19px; height: 126px;
    color: var(--text-grey);
  }
  .person-name { font-size: 20px; font-weight: 700; line-height: 22px; margin-top: -1px; }
  .person-name .surname { color: var(--brand-blue); }
  .person-role { font-size: 17px; line-height: 21px; }
  .contact-list { list-style: none; margin-top: 18px; font-size: 17px; }
  .contact-list li { display: flex; align-items: center; gap: 7px; height: 22.5px; }
  .contact-list svg { width: 12px; height: 12px; fill: var(--brand-blue); flex: none; }
  .licence {
    position: absolute; left: 337px; top: 322px;
    font-size: 17.5px; color: var(--text-grey);
  }
  .tagline {
    position: absolute; left: 0; right: 0; top: 73px;
    text-align: center; font-size: 22px; line-height: 28px;
  }
  .card-back .brand {
    position: absolute; left: 0; right: 0; top: 187px;
    justify-content: center; color: #fff; font-size: 40px; gap: 16px;
  }
  .card-back .brand-mark { width: 66px; height: 66px; background: #fff; }
  .invite {
    position: absolute; left: 0; right: 0; top: 312px;
    text-align: center; font-size: 17.5px;
  }
</style>
</head>
<body>
<main class="canvas">
  <section class="card card-front">
    <div class="brand"><span class="brand-mark"></span>Halvern Property Group</div>
    <div class="contact-block">
      <p class="person-name">Daniel <span class="surname">Marsh</span></p>
      <p class="person-role">Director</p>
      <ul class="contact-list">
        <li><svg viewBox="0 0 24 24" aria-hidden="true"><path d="M6.6 10.8a15.2 15.2 0 0 0 6.6 6.6l2.2-2.2a1 1 0 0 1 1-.25 11.4 11.4 0 0 0 3.6.57 1 1 0 0 1 1 1V20a1 1 0 0 1-1 1A17 17 0 0 1 3 4a1 1 0 0 1 1-1h3.5a1 1 0 0 1 1 1c0 1.25.2 2.45.57 3.57a1 1 0 0 1-.25 1z"/></svg>0400 318 642</li>
        <li><svg viewBox="0 0 24 24" aria-hidden="true"><path d="M2 5h20v14H2z M2 5l10 8 10-8" /></svg>daniel@halvern.com.au</li>
        <li><svg viewBox="0 0 24 24" aria-hidden="true"><path d="M12 2a10 10 0 1 0 0 20 10 10 0 0 0 0-20zm0 2c1 0 2.3 2 2.8 5H9.2C9.7 6 11 4 12 4zM4.3 11h3.8a20 20 0 0 0 0 2H4.3a8 8 0 0 1 0-2zm1 4h3.1c.3 1.5.8 2.8 1.4 3.7A8 8 0 0 1 5.3 15zm0-6a8 8 0 0 1 4.5-3.7c-.6.9-1.1 2.2-1.4 3.7zm6.7 11c-1 0-2.3-2-2.8-5h5.6c-.5 3-1.8 5-2.8 5zm-2.9-7a18 18 0 0 1 0-2h5.8a18 18 0 0 1 0 2zm5.1 5.7c.6-.9 1.1-2.2 1.4-3.7h3.1a8 8 0 0 1-4.5 3.7zM15.9 13a20 20 0 0 0 0-2h3.8a8 8 0 0 1 0 2zm-.3-4c-.3-1.5-.8-2.8-1.4-3.7A8 8 0 0 1 18.7 9z"/></svg>www.halvern.com.au</li>
      </ul>
    </div>
    <p class="licence">Real Estate Lic: 4105932 &amp; 4105933</p>
  </section>

  <section class="card card-back">
    <p class="tagline">Property Development<br>&amp; Site Acquisition Specialists</p>
    <div class="brand"><span class="brand-mark"></span>Halvern Property Group</div>
    <p class="invite">Ask me about our INVESTMENT &amp; PARTNERSHIP opportunities</p>
  </section>
</main>
</body>
</html>
```